Need a new logo/business card for a cafe

I need a new logo and business card for a café. The café is called "Ladle", and we have a reputation for making a high quality cup of espresso coffee. I would like the business card design to reflect this "high quality". Our baristas craft our customers coffee with care to achieve this result. I would like to see designs that include a warm latte brown color. The card will be single sided to allow the rear to be used as a loyalty card which means the design will need to include space for our business address, phone number, and facebook page details. The uploaded logo is already in use on the café front window, and if it can be incorporated or used that would be great, but I am open to completely new designs as well. Thank you.
Updates
Thank you to all for the submissions. There's quite a few I like now, the hardest part will be choosing! I've set up a poll for added feedback from my own contacts and will wait on results from that.
Hello, more great designs coming in, thank you very much. There's quite a few that I really like, so my biggest challenge is going to be choosing one. Thanks again for your time, and I'll get onto the hard task of making that choice. Miriam
Industry/Entity Type
Cafe
Look and feel
Each slider illustrates characteristics of the customer's brand and the style your logo design should communicate.

```html
<!DOCTYPE html>
<html lang="en">
<head>
<meta charset="utf-8">
<title>Ladle Letterhead</title>
<link rel="stylesheet" href="https://fonts.googleapis.com/css2?family=Courier+Prime:wght@400&display=swap">
<style>
  :root {
    --backdrop: #dadada;
    --latte: #a29184;
    --cream: #efecea;
    --band: #050505;
    --mark: #9b8577;
    --ink-light: #f4f1ee;
    --rule: #f1ece8;
  }
  html, body {
    margin: 0;
    padding: 0;
    width: 1200px;
    height: 1000px;
    overflow: hidden;
    background: var(--backdrop);
  }
  .canvas {
    position: relative;
    width: 1200px;
    height: 1000px;
    font-family: "Courier Prime", "Courier New", monospace;
  }
  .sheet {
    position: absolute;
    top: 100px;
    width: 505px;
    height: 818px;
  }
  .sheet--front { left: 47px; background: var(--latte); }
  .sheet--blank { left: 646px; background: var(--cream); }

  .sender {
    position: absolute;
    left: 28px;
    top: 27px;
    color: var(--ink-light);
  }
  .sender__name {
    margin: 0 0 2px;
    font-size: 19px;
    font-weight: 400;
    line-height: 22px;
  }
  .sender__line {
    margin: 0;
    font-size: 14px;
    line-height: 18.5px;
  }
  .sender-rule {
    position: absolute;
    left: 146px;
    top: 117px;
    width: 186px;
    height: 1px;
    background: var(--rule);
  }

  .footer-band {
    position: absolute;
    left: 0;
    top: 638px;
    width: 505px;
    height: 153px;
    background: var(--band);
  }
  .brand {
    position: absolute;
    right: 34px;
    top: 48px;
    display: flex;
    align-items: center;
    gap: 16px;
  }
  .brand__dot {
    width: 18px;
    height: 18px;
    border-radius: 50%;
    background: var(--mark);
  }
  .brand__name {
    color: var(--mark);
    font-size: 54px;
    line-height: 1;
  }
  .web-link {
    position: absolute;
    right: 25px;
    bottom: 7px;
    color: var(--ink-light);
    font-size: 10px;
    letter-spacing: 0.3px;
  }
</style>
</head>
<body>
<div class="canvas">
  <section class="sheet sheet--front">
    <div class="sender">
      <p class="sender__name">Miriam Harlow</p>
      <p class="sender__line">41 Shore Street, Pelican Cove</p>
      <p class="sender__line">New South Wales 2541</p>
      <p class="sender__line">+61 2 5550 1932</p>
    </div>
    <div class="sender-rule"></div>
    <div class="footer-band">
      <div class="brand">
        <span class="brand__dot"></span>
        <span class="brand__name">Ladle</span>
      </div>
      <span class="web-link">www.ladlecafe.com.au/visit</span>
    </div>
  </section>

  <section class="sheet sheet--blank">
    <div class="footer-band">
      <div class="brand">
        <span class="brand__dot"></span>
        <span class="brand__name">Ladle</span>
      </div>
    </div>
  </section>
</div>
</body>
</html>
```